Frostvale Harborline LLC

we need a business card design

Industry/Entity Type

hvac

Contact Information for Business Card

my logo

Requirements
Must have
• my logo and same colors

```html
<!DOCTYPE html>
<html lang="en">
<head>
<meta charset="utf-8">
<title>Frostvale Harborline LLC – Business Card</title>
<link href="https://fonts.googleapis.com/css2?family=Montserrat:wght@400;500;700;800&display=swap" rel="stylesheet">
<style>
  :root {
    --bg: #3a3a3a;
    --card-blue: #0f5fa8;
    --gold: #f6b33d;
    --sky: #22b0e6;
    --white: #ffffff;
  }
  * { box-sizing: border-box; margin: 0; padding: 0; }
  html, body { width: 1200px; height: 875px; overflow: hidden; }
  body {
    background: var(--bg);
    font-family: "Montserrat", sans-serif;
    color: var(--white);
    position: relative;
  }
  .card {
    position: absolute;
    width: 540px;
    height: 310px;
    background: var(--card-blue);
    border-radius: 18px;
    box-shadow: 0 4px 0 var(--gold), 0 18px 30px rgba(0,0,0,0.45);
  }
  .card-front { left: 50px; top: 90px; }
  .card-back { left: 610px; top: 475px; }

  .brand {
    display: flex;
    align-items: center;
    gap: 10px;
  }
  .brand-dot {
    width: 18px; height: 18px;
    border-radius: 50%;
    background: var(--gold);
    flex: none;
  }
  .brand-name {
    font-weight: 800;
    color: var(--white);
    line-height: 1.1;
    text-transform: uppercase;
  }
  .card-front .brand {
    position: absolute;
    left: 0; right: 0; top: 50%;
    transform: translateY(-50%);
    justify-content: center;
  }
  .card-front .brand-name { font-size: 30px; text-align: left; }

  .card-back .brand {
    position: absolute;
    left: 34px; top: 50%;
    transform: translateY(-50%);
    width: 220px;
  }
  .card-back .brand-name { font-size: 19px; }

  .details {
    position: absolute;
    left: 280px; top: 42px;
    width: 230px;
  }
  .person-name {
    font-size: 21px;
    font-weight: 700;
    color: var(--sky);
    letter-spacing: 0.5px;
  }
  .person-role {
    font-size: 13px;
    margin-top: 2px;
  }
  .rule {
    height: 1px;
    background: var(--gold);
    margin: 12px 0;
  }
  .address { font-size: 12.5px; line-height: 1.45; }
  .contact-list { list-style: none; font-size: 12.5px; }
  .contact-list li {
    display: flex; align-items: center; gap: 8px;
    margin-bottom: 6px;
  }
  .contact-list svg { width: 12px; height: 12px; flex: none; }
</style>
</head>
<body>
  <section class="card card-front">
    <div class="brand">
      <span class="brand-dot"></span>
      <span class="brand-name">Frostvale<br>Harborline LLC</span>
    </div>
  </section>

  <section class="card card-back">
    <div class="brand">
      <span class="brand-dot"></span>
      <span class="brand-name">Frostvale<br>Harborline LLC</span>
    </div>
    <div class="details">
      <p class="person-name">DORIAN VELL</p>
      <p class="person-role">Founder</p>
      <div class="rule"></div>
      <p class="address">24 Quarry Hill Rd<br>Northmere XYZ 4120</p>
      <div class="rule"></div>
      <ul class="contact-list">
        <li>
          <svg viewBox="0 0 12 12"><path d="M2 1h2.5l1 3-1.5 1a7 7 0 0 0 3 3l1-1.5 3 1V11c-5 0-9-4-9-9z" fill="var(--gold)"/></svg>
          555.014.0277
        </li>
        <li>
          <svg viewBox="0 0 12 12"><rect x="0.5" y="2" width="11" height="8" fill="var(--gold)"/><path d="M0.5 2l5.5 4.5L11.5 2" fill="none" stroke="var(--card-blue)" stroke-width="1"/></svg>
          info@frostvaleharborline.com
        </li>
        <li>
          <svg viewBox="0 0 12 12"><circle cx="6" cy="6" r="5.2" fill="none" stroke="var(--gold)" stroke-width="1.2"/><path d="M0.8 6h10.4M6 0.8c-3 3-3 7.4 0 10.4M6 0.8c3 3 3 7.4 0 10.4" fill="none" stroke="var(--gold)" stroke-width="1"/></svg>
          www.frostvaleharborline.com
        </li>
      </ul>
    </div>
  </section>
</body>
</html>
```